Business Card for a Dental Office

The design should communicate integrity, quality and reliability. We also want the card look elegant, simple, but still stand out, different from the traditional-dental-office business card.

Industry/Entity Type

Business

```html
<!DOCTYPE html>
<html lang="en">
<head>
<meta charset="utf-8">
<title>Harlow Dental Studio – Business Card</title>
<link href="https://fonts.googleapis.com/css2?family=Open+Sans:wght@400;600;700&display=swap" rel="stylesheet">
<style>
  :root {
    --backdrop: #4a4a4c;
    --card-white: #ffffff;
    --gold: #b99c30;
    --charcoal: #3b3b3d;
    --ink: #1b1b1b;
    --light-text: #f2f2f2;
  }
  * { margin: 0; padding: 0; box-sizing: border-box; }
  html, body {
    width: 1200px; height: 977px; overflow: hidden;
    background: var(--backdrop);
    font-family: "Open Sans", sans-serif;
  }
  .card {
    position: absolute; left: 100px; top: 203px;
    width: 1000px; height: 571px;
    background: var(--card-white);
    overflow: hidden;
    box-shadow: 0 18px 40px rgba(0,0,0,0.35);
  }
  .brand {
    position: absolute; left: 0; right: 0; top: 140px;
    display: flex; justify-content: center; align-items: center; gap: 16px;
  }
  .brand-mark {
    width: 44px; height: 44px; background: var(--gold);
  }
  .brand-name {
    font-weight: 700; font-size: 44px; letter-spacing: 1px;
    color: var(--ink); text-transform: uppercase;
  }
  .name-band {
    position: absolute; left: 0; right: 0; top: 330px; height: 80px;
    background: var(--gold);
    border-bottom: 6px solid var(--card-white);
    box-sizing: content-box;
  }
  .holder-name {
    position: absolute; left: 78px; bottom: 14px;
    font-size: 27px; font-weight: 600; color: var(--card-white);
  }
  .website {
    position: absolute; right: 60px; top: 12px;
    font-size: 17px; color: var(--card-white);
  }
  .contact-band {
    position: absolute; left: 0; right: 0; top: 416px; bottom: 0;
    background: var(--charcoal);
    display: flex; align-items: center;
    padding: 0 60px 0 100px; gap: 0;
    color: var(--light-text); font-size: 19px; line-height: 1.45;
  }
  .contact-group { display: flex; align-items: center; gap: 16px; }
  .contact-group.address { width: 300px; }
  .contact-group.phones { width: 290px; }
  .contact-lines { display: flex; flex-direction: column; gap: 4px; }
  .contact-line { display: flex; align-items: center; gap: 14px; }
  .icon { width: 18px; height: 18px; fill: var(--light-text); flex: none; }
</style>
</head>
<body>
  <article class="card">
    <div class="brand">
      <span class="brand-mark"></span>
      <span class="brand-name">Harlow Dental Studio</span>
    </div>

    <div class="name-band">
      <span class="website">www.harlowdental.com</span>
      <span class="holder-name">Daniel Reyes</span>
    </div>

    <div class="contact-band">
      <div class="contact-group address">
        <svg class="icon" viewBox="0 0 24 24" aria-hidden="true"><path d="M12 2a7 7 0 0 0-7 7c0 5 7 13 7 13s7-8 7-13a7 7 0 0 0-7-7zm0 9.5a2.5 2.5 0 1 1 0-5 2.5 2.5 0 0 1 0 5z"/></svg>
        <div class="contact-lines">
          <span>1847 Maple Row</span>
          <span>Fairview NY 10590</span>
        </div>
      </div>

      <div class="contact-group phones">
        <div class="contact-lines">
          <span class="contact-line">
            <svg class="icon" viewBox="0 0 24 24" aria-hidden="true"><path d="M6.6 10.8a15 15 0 0 0 6.6 6.6l2.2-2.2a1 1 0 0 1 1-.25 11.4 11.4 0 0 0 3.6.57 1 1 0 0 1 1 1V20a1 1 0 0 1-1 1A17 17 0 0 1 3 4a1 1 0 0 1 1-1h3.5a1 1 0 0 1 1 1c0 1.25.2 2.45.57 3.6a1 1 0 0 1-.25 1z"/></svg>
            555.201.4830
          </span>
          <span class="contact-line">
            <svg class="icon" viewBox="0 0 24 24" aria-hidden="true"><path d="M3 8h18v12H3zM7 3h10v5H7z"/></svg>
            555.201.4831
          </span>
        </div>
      </div>

      <div class="contact-group mobile">
        <div class="contact-lines">
          <span class="contact-line">
            <svg class="icon" viewBox="0 0 24 24" aria-hidden="true"><path d="M7 1h10a2 2 0 0 1 2 2v18a2 2 0 0 1-2 2H7a2 2 0 0 1-2-2V3a2 2 0 0 1 2-2zm0 3v14h10V4z"/></svg>
            555.307.6612
          </span>
          <span class="contact-line">
            <svg class="icon" viewBox="0 0 24 24" aria-hidden="true"><path d="M2 5h20v14H2zm2 2v.5l8 5 8-5V7z"/></svg>
            hello@harlowdental.com
          </span>
        </div>
      </div>
    </div>
  </article>
</body>
</html>
```